School Poster

Design so that these can be placed in classrooms across the school.

Attached is another design we have had done. Use a similar theme.

Consider using themes from https://corvalhs.edq.example.au/

please edit Binder1 doc.

Students and teachers

```html
<!DOCTYPE html>
<html lang="en">
<head>
<meta charset="utf-8">
<title>Before You Ask the Teacher – Classroom Poster</title>
<link rel="stylesheet" href="https://fonts.googleapis.com/css2?family=Montserrat:wght@500;600;700;800;900&display=swap">
<style>
:root{
  --navy:#003a70;
  --yellow:#f5e67e;
  --gold:#f7e34a;
  --pale:#e2eff9;
  --red:#e03b3b;
  --white:#ffffff;
}
*{margin:0;padding:0;box-sizing:border-box}
html,body{width:1200px;height:1200px;overflow:hidden;background:var(--white);font-family:"Montserrat",Arial,sans-serif}
.canvas{position:relative;width:1200px;height:1200px;overflow:hidden}
.poster{position:absolute;left:227px;top:70px;width:932px;height:1316px;transform:scale(0.8);transform-origin:0 0;background:var(--white);overflow:hidden;box-shadow:0 4px 14px rgba(0,0,0,.25)}
.abs{position:absolute}
.header-band{left:0;top:0;width:932px;height:147px;background:var(--navy)}
.sub-band{left:0;top:147px;width:932px;height:56px;background:var(--pale)}
.title{left:300px;top:36px;font-weight:900;font-size:47px;line-height:46px;letter-spacing:.5px}
.title .l1{color:var(--gold)}
.title .l2{color:var(--white)}
.subtitle{left:300px;top:157px;font-weight:800;font-size:35px;color:var(--navy)}
.brand-mark{left:120px;top:38px;width:80px;height:80px;border-radius:50%;background:var(--yellow)}
.brand-name{left:70px;top:150px;width:180px;text-align:center;font-weight:800;font-size:22px;color:var(--navy)}

.card{top:254px;width:267px;height:330px;border-radius:18px;background:var(--navy);color:var(--white)}
.card.alt{background:var(--yellow);color:var(--navy)}
.card-icon{top:-36px;left:93px;width:80px;height:80px;border-radius:50%;background:var(--yellow);border:6px solid var(--navy)}
.card.alt .card-icon{background:var(--white)}
.step-tab{left:0;top:66px;width:38px;height:32px;background:var(--gold);color:var(--navy);border-radius:0 6px 6px 0;font-weight:800;font-size:18px;text-align:center;line-height:32px}
.card.alt .step-tab{background:var(--navy);color:var(--gold)}
.card-title{left:68px;top:58px;font-weight:800;font-size:25px;line-height:24px}
.card-rule{left:22px;width:223px;height:1px;background:rgba(255,255,255,.7)}
.card.alt .card-rule{background:rgba(0,58,112,.45)}
.card-lead{left:34px;top:134px;width:210px;font-weight:700;font-size:15px;line-height:20px;color:var(--gold)}
.card.alt .card-lead{color:var(--navy)}
.checks{list-style:none;left:30px;width:235px;font-weight:600;font-size:11px;line-height:13px}
.checks li{position:relative;padding-left:17px;margin-bottom:9px}
.checks li::before{content:"";position:absolute;left:0;top:1px;width:10px;height:10px;border-radius:50%;background:var(--gold)}
.card.alt .checks li::before{background:var(--navy)}
.checks li::after{content:"";position:absolute;left:3px;top:3px;width:3px;height:5px;border:solid var(--navy);border-width:0 1.5px 1.5px 0;transform:rotate(45deg)}
.card.alt .checks li::after{border-color:var(--yellow)}
.card-note{left:22px;top:284px;font-weight:600;font-size:11px}

.pill{top:605px;width:215px;height:47px;border-radius:24px;font-weight:800;font-size:21px;text-align:center;line-height:47px}
.pill.light{background:var(--yellow);color:var(--navy)}
.pill.dark{background:var(--navy);color:var(--white)}

.ai-head{left:35px;top:678px;width:862px;height:47px;background:var(--navy);border-radius:12px 12px 0 0;color:var(--gold);font-weight:800;font-size:28px;letter-spacing:3px;text-align:center;line-height:49px}
.ai-body{left:35px;top:725px;width:862px;height:400px;background:var(--pale)}
.base-band{left:0;top:1117px;width:932px;height:199px;background:var(--navy)}
.col-head{font-weight:800;font-size:23px;line-height:23px;color:var(--navy)}
.ai-list{list-style:none;font-weight:600;font-size:14px;line-height:12px;color:var(--navy)}
.ai-list li{position:relative;padding-left:23px;margin-bottom:12px}
.ai-list li::before{content:"";position:absolute;left:0;top:-1px;width:12px;height:12px;border-radius:50%;background:var(--navy)}
.ai-list li::after{content:"";position:absolute;left:4px;top:1px;width:3px;height:6px;border:solid var(--white);border-width:0 1.5px 1.5px 0;transform:rotate(45deg)}
.cannot-pill{left:318px;top:913px;width:298px;height:40px;border-radius:20px;background:var(--navy);color:var(--white);font-weight:700;font-size:23px;text-align:center;line-height:40px}
.no-box{top:986px;width:179px;height:167px;border-radius:14px;background:var(--yellow);border:1.5px solid var(--navy);display:flex;align-items:center;justify-content:center;text-align:center;padding:24px 12px 0;font-weight:700;font-size:16px;line-height:22px;color:var(--navy)}
.tagline{left:162px;top:1176px;width:608px;height:35px;border-radius:18px;background:var(--yellow);color:var(--navy);font-weight:700;font-size:17px;text-align:center;line-height:35px}
.refs{left:60px;width:812px;text-align:center;color:var(--white);font-weight:700;font-size:9.5px;line-height:13px;text-transform:uppercase}
</style>
</head>
<body>
<div class="canvas">
<article class="poster">
  <div class="abs header-band"></div>
  <div class="abs sub-band"></div>
  <div class="abs brand-mark"></div>
  <div class="abs brand-name">CORVAL HIGH</div>
  <h1 class="abs title"><span class="l1">BEFORE YOU ASK</span><br><span class="l2">THE TEACHER...</span></h1>
  <h2 class="abs subtitle">TRY THESE STEPS FIRST!</h2>

  <section class="abs card" style="left:45px">
    <div class="abs card-icon" role="img" aria-label="Thinking head icon"></div>
    <div class="abs step-tab">1</div>
    <h3 class="abs card-title">THINK<br>AT FIRST</h3>
    <div class="abs card-rule" style="top:125px"></div>
    <p class="abs card-lead">Don't give up straight away.</p>
    <div class="abs card-rule" style="top:183px"></div>
    <ul class="abs checks" style="top:209px">
      <li>Read the question carefully.</li>
      <li>Identify what you already know.</li>
      <li>Try a strategy you've used before.</li>
      <li>Give yourself thinking time.</li>
    </ul>
  </section>

  <section class="abs card alt" style="left:333px">
    <div class="abs card-icon" role="img" aria-label="Checklist icon"></div>
    <div class="abs step-tab">2</div>
    <h3 class="abs card-title">CHECK YOUR<br>SUPPORTS</h3>
    <div class="abs card-rule" style="top:125px"></div>
    <p class="abs card-lead">Before asking for help, check:</p>
    <div class="abs card-rule" style="top:183px"></div>
    <ul class="abs checks" style="top:200px">
      <li>Learning goal and success criteria.</li>
      <li>Worked examples.</li>
      <li>Class notes.</li>
      <li>Classroom displays.</li>
      <li>ClassHub resources.</li>
      <li>Task sheet and instructions.</li>
    </ul>
  </section>

  <section class="abs card" style="left:620px">
    <div class="abs card-icon" role="img" aria-label="People asking each other icon"></div>
    <div class="abs step-tab">3</div>
    <h3 class="abs card-title">ASK 3<br>BEFORE ME</h3>
    <div class="abs card-rule" style="top:125px"></div>
    <p class="abs card-lead">Ask three sources before asking the teacher:</p>
    <div class="abs card-rule" style="top:183px"></div>
    <ul class="abs checks" style="top:200px">
      <li>A person (partner or neighbour)</li>
      <li>A place (notes, display, ClassHub)</li>
      <li>A resource (worked example, task sheet)</li>
    </ul>
    <p class="abs card-note">Then ask the teacher if you still need help.</p>
  </section>

  <div class="abs pill light" style="left:55px">WE BELIEVE</div>
  <svg class="abs" style="left:285px;top:614px" width="58" height="30" viewBox="0 0 58 30" aria-hidden="true"><path d="M2 2h11l13 13-13 13H2l13-13z M28 2h11l13 13-13 13H28l13-13z" fill="var(--gold)"/></svg>
  <div class="abs pill dark" style="left:358px">WE STRIVE</div>
  <svg class="abs" style="left:588px;top:614px" width="58" height="30" viewBox="0 0 58 30" aria-hidden="true"><path d="M2 2h11l13 13-13 13H2l13-13z M28 2h11l13 13-13 13H28l13-13z" fill="var(--gold)"/></svg>
  <div class="abs pill light" style="left:655px">WE ACHIEVE</div>

  <div class="abs ai-body"></div>
  <div class="abs base-band"></div>
  <h2 class="abs ai-head">USING AI &amp; OTHER TOOLS RESPONSIBLY</h2>

  <h3 class="abs col-head" style="left:80px;top:752px">What You Must Do:</h3>
  <ul class="abs ai-list" style="left:80px;top:794px;width:350px">
    <li>Complete your own work</li>
    <li>Demonstrate your progress (drafts, notes, planning, revisions)</li>
    <li>Use feedback to improve your work</li>
    <li>Demonstrate your understanding of the ideas in your submission</li>
  </ul>

  <h3 class="abs col-head" style="left:460px;top:743px">What AI can help you do<br>(when approved by your teacher)</h3>
  <ul class="abs ai-list" style="left:460px;top:807px;width:420px">
    <li>Brainstorm ideas</li>
    <li>Check spelling, grammar and clarity</li>
    <li>Read your work aloud using text-to-speech tools</li>
    <li>Help identify areas for improvement in a draft</li>
  </ul>

  <svg class="abs" style="left:0;top:0" width="932" height="1316" aria-hidden="true">
    <path d="M88 986V933H318M616 933H842V986" fill="none" stroke="var(--navy)" stroke-width="1.5"/>
  </svg>
  <div class="abs cannot-pill">What You Cannot Do</div>

  <div class="abs no-box" style="left:71px">Submit<br>AI<br>generated<br>work as<br>your own</div>
  <div class="abs no-box" style="left:275px">Copy &amp; paste AI responses without acknowledging or adapting them</div>
  <div class="abs no-box" style="left:484px">Use<br>AI tools<br>to complete<br>the whole<br>task for you</div>
  <div class="abs no-box" style="left:689px">Submit work that does not demonstrate your understanding</div>

  <svg class="abs" style="left:0;top:0" width="932" height="1316" aria-hidden="true">
    <g stroke="var(--white)" stroke-width="5" stroke-linecap="round">
      <circle cx="161" cy="984" r="24" fill="var(--red)" stroke="none"/><path d="M152 975l18 18M170 975l-18 18"/>
      <circle cx="365" cy="984" r="24" fill="var(--red)" stroke="none"/><path d="M356 975l18 18M374 975l-18 18"/>
      <circle cx="573" cy="984" r="24" fill="var(--red)" stroke="none"/><path d="M564 975l18 18M582 975l-18 18"/>
      <circle cx="779" cy="984" r="24" fill="var(--red)" stroke="none"/><path d="M770 975l18 18M788 975l-18 18"/>
    </g>
  </svg>

  <p class="abs tagline">If you didn't create, develop and understand it, it isn't your work.</p>

  <p class="abs refs" style="top:1228px">Harlow, M. 2025. "Why students don't ask for help- and how to change that" downloaded on 24/04/2026 from<br>https://www.teachwell.example.org/article/students-ask-help/</p>
  <p class="abs refs" style="top:1268px">CELR, 2024. "Supporting self-regulated learning", downloaded on 24/04/2026 from<br>https://www.celr.example.au/files/2024-02/supporting-self-regulated-learning.pdf</p>
</article>
</div>
</body>
</html>
```